Business card design needed

I would like a one sided black business card with the information provided above. Refer to my website www.brightvolleyracquets.com.au for an example of colors I have used for my site, would like to keep this consistent for my business cards also, I will upload my logo below.

I am a new small business that provides tennis customers with racquet re stringing, tennis strings and accessories.

Industry/Entity Type

Small Business

Contact Information for Business Card

Bright Volley Tennis

Owen Whitby
Managing Director

brightvolleyracquets@mailbox.example
www.brightvolleyracquets.com.au
0491 726 305

Racquet Restringing/Tennis Strings/Accessories

Requirements
Must have
• Must have my logo and card must be black

```html
<!DOCTYPE html>
<html lang="en">
<head>
<meta charset="utf-8">
<title>Bright Volley Tennis – Business Card</title>
<link rel="stylesheet" href="https://fonts.googleapis.com/css2?family=Questrial&display=swap">
<style>
  :root {
    --backdrop: #e8e5e1;
    --card-black: #000000;
    --lime: #b5d334;
    --text-light: #e6e6e6;
    --icon-grey: #cfcfcf;
  }
  * { box-sizing: border-box; margin: 0; padding: 0; }
  html, body {
    width: 1200px;
    height: 475px;
    overflow: hidden;
    background: var(--backdrop);
    font-family: "Questrial", "Helvetica Neue", Arial, sans-serif;
  }
  .canvas {
    position: relative;
    width: 1200px;
    height: 475px;
  }
  .card {
    position: absolute;
    top: 81px;
    width: 547px;
    height: 312px;
    background: var(--card-black);
    overflow: hidden;
  }
  .card--front { left: 23px; }
  .card--back { left: 602px; }

  .brand {
    position: absolute;
    display: flex;
    align-items: center;
    gap: 12px;
    color: var(--lime);
    font-size: 28px;
    letter-spacing: 1px;
    text-transform: uppercase;
    white-space: nowrap;
  }
  .brand__dot {
    width: 34px;
    height: 34px;
    border-radius: 50%;
    background: var(--lime);
    flex: none;
  }
  .card--front .brand { left: 38px; top: 58px; }
  .card--back .brand { left: 50%; top: 110px; transform: translateX(-50%); }

  .holder {
    position: absolute;
    left: 45px;
    top: 170px;
    color: var(--lime);
    white-space: nowrap;
  }
  .holder__name { font-size: 20px; letter-spacing: 0.5px; }
  .holder__role { font-size: 14px; margin-left: 4px; }

  .contacts {
    position: absolute;
    left: 45px;
    top: 219px;
    list-style: none;
  }
  .contacts__item {
    display: flex;
    align-items: center;
    gap: 12px;
    height: 19px;
    color: var(--text-light);
    font-size: 14px;
    letter-spacing: 0.3px;
  }
  .contacts__icon { width: 11px; height: 11px; flex: none; }

  .accent-bar {
    position: absolute;
    left: 0;
    bottom: 0;
    width: 100%;
    height: 12px;
    background: var(--lime);
  }

  .site {
    position: absolute;
    left: 0;
    width: 100%;
    top: 259px;
    text-align: center;
    color: var(--text-light);
    font-size: 14px;
    letter-spacing: 2px;
  }
</style>
</head>
<body>
<main class="canvas">
  <section class="card card--front" aria-label="Card front">
    <div class="brand"><span class="brand__dot"></span>Bright Volley Tennis</div>
    <p class="holder"><span class="holder__name">OWEN WHITBY,</span> <span class="holder__role">Managing Director</span></p>
    <ul class="contacts">
      <li class="contacts__item">
        <svg class="contacts__icon" viewBox="0 0 12 12" aria-hidden="true"><path d="M2.5 1 L4.5 1 L5.2 3.6 L4 4.6 Q5 7 7.4 8 L8.4 6.8 L11 7.5 L11 9.5 Q10 11 8.5 11 Q1 9.5 1 3.5 Q1 2 2.5 1Z" fill="var(--icon-grey)"/></svg>
        0491 726 305
      </li>
      <li class="contacts__item">
        <svg class="contacts__icon" viewBox="0 0 12 12" aria-hidden="true"><rect x="0.5" y="2.5" width="11" height="7.5" fill="var(--icon-grey)"/><path d="M0.5 2.5 L6 7 L11.5 2.5" stroke="#000" stroke-width="1" fill="none"/></svg>
        brightvolleyracquets@mailbox.example
      </li>
      <li class="contacts__item">
        <svg class="contacts__icon" viewBox="0 0 12 12" aria-hidden="true"><g fill="none" stroke="var(--icon-grey)" stroke-width="1.1"><circle cx="6" cy="6" r="5"/><ellipse cx="6" cy="6" rx="2.2" ry="5"/><path d="M1 6 H11 M2 3.5 H10 M2 8.5 H10"/></g></svg>
        www.brightvolleyracquets.com.au
      </li>
    </ul>
    <div class="accent-bar"></div>
  </section>

  <section class="card card--back" aria-label="Card back">
    <div class="brand"><span class="brand__dot"></span>Bright Volley Tennis</div>
    <p class="site">www.brightvolleyracquets.com.au</p>
  </section>
</main>
</body>
</html>
```